Brightfen Business Card Redesign & Logo Update

We need to update our business cards to something more modern and fresh. Brightfen can provide the current color schemes and old design examples, but welcome creativity in helping us with this redesign. PLEASE NOTE that we no longer utilize the "tree" and/or "leaf" imagery in our branding. If able would apprecaite an update on the quality of our "words only" logo in Ai. / PNG formats too.

Target Market(s)

Investors, landowners, corporate partners, contractors

Industry/Entity Type

Environmental Restoration & Conservation

Contact Information for Business Card

Logo, persons name, title, mailing address, phone and email, website url

Font styles to use
Other font styles liked:
• Merriweather

Requirements
Nice to have
• Logo, persons name, title, mailing address, phone and email, website url, but open to ideams
Should not have
• No all back backgrounds

```html
<!DOCTYPE html>
<html lang="en">
<head>
<meta charset="utf-8">
<title>Brightfen Business Card</title>
<link rel="stylesheet" href="https://fonts.googleapis.com/css2?family=Oswald:wght@500;700&family=Open+Sans:wght@400;700&display=swap">
<style>
  :root {
    --stage: #d9dadc;
    --card: #3a3d43;
    --card-edge: #4a4e55;
    --orange: #f08122;
    --green: #1a9a48;
    --white: #ffffff;
    --muted: #eceef0;
  }
  * { margin: 0; padding: 0; box-sizing: border-box; }
  html, body { width: 1200px; height: 780px; overflow: hidden; }
  body {
    background: var(--stage);
    font-family: "Open Sans", sans-serif;
    position: relative;
  }
  .card {
    position: absolute;
    top: 236px;
    width: 540px;
    height: 308px;
    background: linear-gradient(160deg, var(--card-edge) 0%, var(--card) 70%);
    box-shadow: 0 10px 28px rgba(0,0,0,.25);
  }
  .card--front { left: 40px; }
  .card--back { left: 620px; }

  .wordmark {
    font-family: "Oswald", sans-serif;
    font-weight: 700;
    color: var(--green);
    text-transform: uppercase;
    line-height: 1;
    letter-spacing: 1px;
  }
  .tagline {
    font-family: "Oswald", sans-serif;
    font-weight: 500;
    color: var(--white);
    text-transform: uppercase;
    line-height: 1;
    letter-spacing: .5px;
  }
  .lockup { position: absolute; }
  .card--front .lockup {
    left: 0; right: 0;
    top: 50%;
    transform: translateY(-50%);
    text-align: center;
  }
  .card--front .wordmark { font-size: 92px; }
  .card--front .tagline { font-size: 25px; margin-top: 10px; }

  .card--back .lockup { left: 36px; top: 28px; }
  .card--back .wordmark { font-size: 48px; }
  .card--back .tagline { font-size: 14px; margin-top: 6px; }

  .person {
    position: absolute;
    left: 36px;
    top: 132px;
  }
  .person__name {
    font-weight: 700;
    font-size: 24px;
    line-height: 1.1;
  }
  .person__first { color: var(--orange); }
  .person__last { color: var(--green); }
  .person__title {
    color: var(--muted);
    font-size: 15px;
    margin-top: 4px;
    padding-left: 14px;
  }
  .divider {
    position: absolute;
    left: 36px;
    right: 36px;
    top: 204px;
    height: 1.5px;
    background: var(--white);
  }
  .contacts {
    position: absolute;
    left: 36px;
    right: 36px;
    top: 218px;
    display: grid;
    grid-template-columns: 1fr 1fr;
    row-gap: 12px;
    column-gap: 20px;
    list-style: none;
  }
  .contacts__item {
    display: flex;
    align-items: center;
    gap: 8px;
    color: var(--muted);
    font-size: 12.5px;
    white-space: nowrap;
  }
  .contacts__icon { width: 15px; height: 15px; flex: none; }
</style>
</head>
<body>
  <section class="card card--front" aria-label="Card front">
    <div class="lockup">
      <p class="wordmark">Brightfen</p>
      <p class="tagline">Environmental Credit Company</p>
    </div>
  </section>

  <section class="card card--back" aria-label="Card back">
    <div class="lockup">
      <p class="wordmark">Brightfen</p>
      <p class="tagline">Environmental Credit Company</p>
    </div>

    <div class="person">
      <p class="person__name"><span class="person__first">Lena</span> <span class="person__last">Marsh</span></p>
      <p class="person__title">Managing Director</p>
    </div>

    <div class="divider"></div>

    <ul class="contacts">
      <li class="contacts__item">
        <svg class="contacts__icon" viewBox="0 0 24 24" aria-hidden="true">
          <path fill="#f08122" d="M6.6 10.8a15.2 15.2 0 0 0 6.6 6.6l2.2-2.2c.3-.3.7-.4 1-.2 1.1.4 2.3.6 3.6.6.6 0 1 .4 1 1V20c0 .6-.4 1-1 1A17 17 0 0 1 3 4c0-.6.4-1 1-1h3.5c.6 0 1 .4 1 1 0 1.3.2 2.5.6 3.6.1.3 0 .7-.2 1l-2.3 2.2z"/>
        </svg>
        <span>+469-555-0142</span>
      </li>
      <li class="contacts__item">
        <svg class="contacts__icon" viewBox="0 0 24 24" aria-hidden="true">
          <rect x="2" y="5" width="20" height="14" rx="1.5" fill="#f08122"/>
          <path d="M3 6.5l9 6.5 9-6.5" fill="none" stroke="#3a3d43" stroke-width="1.8"/>
        </svg>
        <span>info@brightfen.com</span>
      </li>
      <li class="contacts__item">
        <svg class="contacts__icon" viewBox="0 0 24 24" aria-hidden="true">
          <path fill="#f08122" d="M12 2a7 7 0 0 0-7 7c0 5.2 7 13 7 13s7-7.8 7-13a7 7 0 0 0-7-7z"/>
          <circle cx="12" cy="9" r="2.6" fill="#3a3d43"/>
        </svg>
        <span>1200 Meadow Lane, Dallas, TX 75201</span>
      </li>
      <li class="contacts__item">
        <svg class="contacts__icon" viewBox="0 0 24 24" aria-hidden="true">
          <circle cx="12" cy="12" r="10" fill="#f08122"/>
          <path d="M2 12h20M12 2c3 3 3 17 0 20M12 2c-3 3-3 17 0 20" fill="none" stroke="#3a3d43" stroke-width="1.5"/>
        </svg>
        <span>www.brightfen.com</span>
      </li>
    </ul>
  </section>
</body>
</html>
```